Business Cards for IT Consulting Company (Managed Service Provider)

I am looking to have some business cards printed and would like some designs. We are an IT Consulting company based in Vancouver BC. I would like a nice clean and modern look to the cards. I have uploaded all the versions of my logo so parts can be used as needed. Here is a snippit from our website homepage:

Quillbrook Networks Ltd. is an IT Solutions Partner located in Vancouver BC, Canada. We offer IT solutions and support to customers in the greater Vancouver Area. With expertise in Microsoft platforms, as well as Linux and Mac OSX and over 12 years experience in the IT industry, Quillbrook Networks is dedicated to offering our clients top quality service and products. We take pride in the solutions we offer our customers. The greatest compliment a client can give us is to recommend our services.

Quillbrook Networks Ltd. offers a wide range of IT services from onsite service to remote support and managed service solutions. This allows clients to choose the support path that best suits their company’s needs. Supporting many different sized companies from small to enterprise level over the past 12 years Quillbrook Networks has the experience and expertise needed to ensure things run smoothly. Allowing our clients to focus on doing business.

Revolutionizing the way IT services are delivered.

Quillbrook Networks is dedicated to providing our clients with IT solutions that work and grow with them for years to come. This philosophy helps save money in the long run instead of replacing equipment constantly. Far too often IT solutions are not well thought out and while possibly solving the problem at hand, require replacement due to growth or quality within a very short time frame. Quillbrook Networks takes pride in providing solutions that will last and be able to accommodate growth without the need for replacement.

Industry/Entity Type

Information Technology

Contact Information for Business Card

Quillbrook Networks Ltd.
(Employee Name)
Eml: (Employees Email Address)
Web: quillbrook.me
Ph: 604-555-0148

Font styles to use
Serif
Sans Serif

Requirements
Must have
• The Company logo and company colors.
Nice to have
• - Our tag line: "Revolutionizing IT Services" or "Revolutionizing the way IT services are delivered."
• - Also I really like the idea of nature and technology together blending which is sort of where my logo came from so integrating that somehow onto the business cards would be great.

```html
<!DOCTYPE html>
<html lang="en">
<head>
<meta charset="utf-8">
<title>Quillbrook Networks Ltd. – Business Cards</title>
<link rel="stylesheet" href="https://fonts.googleapis.com/css2?family=Montserrat:wght@600;700&family=Roboto:ital,wght@0,400;1,400&display=swap">
<style>
  :root {
    --backdrop: #aaa8a9;
    --brand-blue: #1a8fd6;
    --brand-blue-deep: #1784c6;
    --divider-grey: #555a5e;
    --card-white: #f4f4f4;
    --text-grey: #454545;
    --title-grey: #555555;
    --white: #ffffff;
  }
  * { margin: 0; padding: 0; box-sizing: border-box; }
  html, body {
    width: 1200px;
    height: 1200px;
    overflow: hidden;
    background: var(--backdrop);
  }
  .canvas {
    position: relative;
    width: 1200px;
    height: 1200px;
  }
  .card {
    position: absolute;
    width: 712px;
    height: 419px;
  }

  /* Front */
  .card-front {
    left: 238px;
    top: 118px;
    background: var(--brand-blue);
  }
  .front-pattern {
    position: absolute;
    inset: 0;
    background: linear-gradient(135deg, var(--brand-blue) 0%, var(--brand-blue-deep) 100%);
  }
  .front-brand {
    position: absolute;
    left: 110px;
    top: 158px;
    display: flex;
    align-items: center;
    gap: 22px;
  }
  .brand-square {
    width: 56px;
    height: 56px;
    background: var(--white);
  }
  .brand-name {
    font-family: "Montserrat", sans-serif;
    font-weight: 700;
    line-height: 1.05;
    letter-spacing: 0.5px;
  }
  .front-brand .brand-name {
    color: var(--white);
    font-size: 38px;
  }

  /* Back */
  .card-back {
    left: 231px;
    top: 644px;
    width: 711px;
    height: 417px;
    background: var(--card-white);
  }
  .back-band {
    position: absolute;
    left: 0;
    top: 0;
    width: 60px;
    height: 100%;
    background: var(--brand-blue);
  }
  .back-divider {
    position: absolute;
    left: 60px;
    top: 0;
    width: 7px;
    height: 100%;
    background: var(--divider-grey);
  }
  .back-brand {
    position: absolute;
    left: 107px;
    top: 58px;
    display: flex;
    align-items: center;
    gap: 18px;
  }
  .back-brand .brand-square {
    width: 48px;
    height: 48px;
    background: var(--brand-blue);
  }
  .back-brand .brand-name {
    color: var(--brand-blue);
    font-size: 34px;
  }
  .person {
    position: absolute;
    left: 106px;
    top: 203px;
  }
  .person-name {
    font-family: "Montserrat", sans-serif;
    font-weight: 700;
    font-size: 25px;
    color: var(--brand-blue);
  }
  .person-title {
    margin-top: 4px;
    font-family: "Roboto", sans-serif;
    font-style: italic;
    font-size: 16px;
    color: var(--title-grey);
  }
  .contact-list {
    position: absolute;
    left: 106px;
    top: 294px;
    list-style: none;
  }
  .contact-item {
    display: flex;
    align-items: center;
    height: 27px;
    font-family: "Roboto", sans-serif;
    font-size: 17px;
    color: var(--text-grey);
  }
  .contact-icon {
    width: 17px;
    height: 17px;
    margin-right: 18px;
    fill: var(--brand-blue);
  }
</style>
</head>
<body>
<main class="canvas">

  <section class="card card-front" aria-label="Business card front">
    <div class="front-pattern" role="img" aria-label="Subtle tonal pattern of outlined hexagonal cubes across the blue background"></div>
    <div class="front-brand">
      <span class="brand-square" aria-hidden="true"></span>
      <span class="brand-name">Quillbrook<br>Networks Ltd.</span>
    </div>
  </section>

  <section class="card card-back" aria-label="Business card back">
    <div class="back-band"></div>
    <div class="back-divider"></div>

    <div class="back-brand">
      <span class="brand-square" aria-hidden="true"></span>
      <span class="brand-name">Quillbrook<br>Networks Ltd.</span>
    </div>

    <div class="person">
      <p class="person-name">Daniel Hart</p>
      <p class="person-title">Managing Director</p>
    </div>

    <ul class="contact-list">
      <li class="contact-item">
        <svg class="contact-icon" viewBox="0 0 20 20" aria-hidden="true">
          <path d="M2 7c0-3 3-4 8-4s8 1 8 4v1h-4V6.5c-1-.5-2.5-.7-4-.7s-3 .2-4 .7V8H2z"/>
          <path d="M5 10h10l2 7H3z"/>
        </svg>
        <span>604-555-0148</span>
      </li>
      <li class="contact-item">
        <svg class="contact-icon" viewBox="0 0 20 20" aria-hidden="true">
          <circle cx="10" cy="10" r="8" fill="none" stroke="var(--brand-blue)" stroke-width="1.8"/>
          <ellipse cx="10" cy="10" rx="3.5" ry="8" fill="none" stroke="var(--brand-blue)" stroke-width="1.5"/>
          <path d="M2 10h16M3.5 6h13M3.5 14h13" stroke="var(--brand-blue)" stroke-width="1.3"/>
        </svg>
        <span>www.quillbrook.me</span>
      </li>
      <li class="contact-item">
        <svg class="contact-icon" viewBox="0 0 20 20" aria-hidden="true">
          <path d="M1 4h18v12H1z"/>
          <path d="M1.5 4.5 10 11l8.5-6.5M1.5 15.5 7.5 9.5M18.5 15.5l-6-6" fill="none" stroke="var(--card-white)" stroke-width="1.4"/>
        </svg>
        <span>support@quillbrook.me</span>
      </li>
    </ul>
  </section>

</main>
</body>
</html>
```